Gardening and life coaching business card design

I need business cards for a new company in the heart of the Ozarks at the Lake of the Ozarks. Maple Hollow Unlimited's mission is to teach the world to fish. We provide fresh local fish and produce using permaculture methods. We work with nature and the flow to create more harmony and less impact. We also coach others who are ready to make this transition. We specialize in microgreens and Aquaculture systems. I would like to make Maple Hollow Unlimited come alive with green vines and purple flowers I wold like Maple Hollow Unlimited to be in green and the rest of the lettering to be in purple. The feel of the card should be that of the Garden of Eden.

Life Coaching

Maple Hollow Unlimited
Owner/Operator Dorothea Fenwick
Contact Info:
(555) 214-0683
maplehollowunlimited.com
maplehollowunlimited is also on FB

```html
<!DOCTYPE html>
<html lang="en">
<head>
<meta charset="utf-8">
<title>Maple Hollow Unlimited – Business Card</title>
<link href="https://fonts.googleapis.com/css2?family=Arimo&family=Tinos&display=swap" rel="stylesheet">
<style>
  :root {
    --page-bg: #ececea;
    --card-shadow: rgba(0, 0, 0, 0.18);
    --photo-top: #f3f2ee;
    --photo-leaf: #dfe4d4;
    --photo-mid: #d9cfca;
    --photo-stem: #b79b98;
    --band-green-light: #47c56f;
    --band-green: #2bb552;
    --stripe-black: #111111;
    --stripe-white: #ffffff;
    --ink: #1a1a1a;
    --ink-soft: #2a2a2a;
  }
  * { margin: 0; padding: 0; box-sizing: border-box; }
  html, body {
    width: 1200px;
    height: 914px;
    overflow: hidden;
    background: var(--page-bg);
  }
  .canvas {
    position: relative;
    width: 1200px;
    height: 914px;
  }
  .card {
    position: absolute;
    width: 560px;
    height: 320px;
    overflow: hidden;
    box-shadow: 0 6px 18px var(--card-shadow);
  }
  .card--brand { left: 560px; top: 90px; }
  .card--contact { left: 80px; top: 500px; }

  .card__photo {
    position: absolute;
    inset: 0;
    background:
      radial-gradient(ellipse at 30% 20%, var(--photo-leaf) 0%, transparent 55%),
      radial-gradient(ellipse at 75% 35%, var(--photo-leaf) 0%, transparent 50%),
      linear-gradient(180deg, var(--photo-top) 0%, var(--photo-top) 22%, var(--photo-mid) 55%, var(--photo-stem) 100%);
  }

  .brand-name {
    position: absolute;
    font-family: "Tinos", "Times New Roman", serif;
    color: var(--ink);
    white-space: nowrap;
  }
  .card--brand .brand-name {
    left: 190px;
    top: 132px;
    font-size: 32px;
    transform: rotate(8deg);
    transform-origin: left center;
  }

  .card__band {
    position: absolute;
    inset: 0;
    width: 560px;
    height: 320px;
  }
  .card--contact .brand-name {
    left: 150px;
    top: 240px;
    font-size: 31px;
    transform: rotate(7deg);
    transform-origin: left center;
  }

  .person {
    position: absolute;
    left: 262px;
    top: 62px;
    font-family: "Arimo", Arial, sans-serif;
    color: var(--ink-soft);
    text-align: center;
  }
  .person__name { font-size: 22px; line-height: 1.1; }
  .person__role { font-size: 11px; }

  .contact-list {
    position: absolute;
    left: 210px;
    top: 140px;
    list-style: none;
    font-family: "Arimo", Arial, sans-serif;
    font-size: 16px;
    line-height: 1.2;
    color: var(--ink-soft);
  }
  .contact-list li:first-child { padding-left: 50px; }
  .contact-list li:last-child { padding-left: 12px; }
</style>
</head>
<body>
<main class="canvas">

  <section class="card card--brand" aria-label="Business card front">
    <div class="card__photo" role="img" aria-label="Soft, faded photograph of a tray of young microgreens with pale leaves and reddish stems"></div>
    <h1 class="brand-name">Maple Hollow Unlimited</h1>
  </section>

  <section class="card card--contact" aria-label="Business card back">
    <div class="card__photo" role="img" aria-label="Soft, faded photograph of a tray of young microgreens with pale leaves and reddish stems"></div>

    <svg class="card__band" viewBox="0 0 560 320" aria-hidden="true">
      <defs>
        <linearGradient id="bandGreen" x1="0" y1="0" x2="1" y2="1">
          <stop offset="0" stop-color="var(--band-green-light)"/>
          <stop offset="1" stop-color="var(--band-green)"/>
        </linearGradient>
      </defs>
      <path d="M0 150 C 150 230, 330 250, 560 212 L560 320 L0 320 Z" fill="var(--stripe-black)"/>
      <path d="M0 158 C 150 240, 330 262, 560 226 L560 320 L0 320 Z" fill="var(--stripe-white)"/>
      <path d="M0 170 C 150 254, 330 278, 560 240 L560 320 L0 320 Z" fill="url(#bandGreen)"/>
    </svg>

    <div class="person">
      <p class="person__name">Dorothea Fenwick</p>
      <p class="person__role">Owner/Operator</p>
    </div>

    <ul class="contact-list">
      <li>P: (555) 214-0683</li>
      <li>w: maplehollowunlimited.com</li>
      <li>f: maplehollowunlimited</li>
    </ul>

    <p class="brand-name">Maple Hollow Unlimited</p>
  </section>

</main>
</body>
</html>
```